Business card design for Automotive workshop

We need a business card for a new automotive repair and tyre shop called Keelstone Prime Automotive located in New Zealand. We are a clean, modern and fresh workshop and company.

Front needs to feature logo,
my name:
Marlo Fenwicke (director)

Address:
48 Tarn Lane
Ravensmere 3598

Phone: 07 594 2713
Mobile: 027 451 9362
Email: office@keelstoneautomotive.example.nz
Website: keelstoneautomotive.example.nz

Back needs to feature an area to write down appointment details, date and time.

Also feature a list of jobs and work we do such as,
Vehicle Servicing
All Mechanical Repairs
Warrant of Fitness
Tyres & Wheel Alignments
Automotive Diagnostics
Automotive Parts & Supplies

```html
<!DOCTYPE html>
<html lang="en">
<head>
<meta charset="utf-8">
<title>Keelstone Prime Automotive – Business Card</title>
<link rel="stylesheet" href="https://fonts.googleapis.com/css2?family=Roboto:wght@400;500;700&display=swap">
<style>
  :root {
    --bg: #3a3a3a;
    --card: #000000;
    --red: #ec2227;
    --ink: #000000;
  }
  * { margin: 0; padding: 0; box-sizing: border-box; }
  html, body { width: 1200px; height: 750px; overflow: hidden; }
  body {
    background: radial-gradient(ellipse at 50% 40%, #555 0%, #3a3a3a 55%, #262626 100%);
    font-family: "Roboto", Arial, sans-serif;
    color: var(--red);
    position: relative;
  }
  .card {
    position: absolute;
    width: 560px;
    height: 328px;
    background: var(--card);
    border-radius: 32px;
    overflow: hidden;
    box-shadow: 0 4px 10px rgba(0,0,0,.45);
  }
  .card--front { left: 38px; top: 186px; }
  .card--back  { left: 610px; top: 187px; }

  .block { position: absolute; background: var(--red); }
  .card--front .block { left: 323px; width: 162px; }
  .card--back  .block { left: 335px; width: 163px; }
  .block--top { top: 0; height: 87px; }
  .block--bottom { top: 240px; bottom: 0; }

  .brand {
    position: absolute;
    width: 230px;
    top: 142px;
    text-align: center;
    font-weight: 700;
    font-size: 19px;
    line-height: 21px;
    letter-spacing: 1.5px;
    text-transform: uppercase;
    color: var(--red);
  }
  .card--front .brand { left: 289px; }
  .card--back  .brand { left: 302px; }

  .person { position: absolute; left: 21px; top: 66px; }
  .person__name {
    display: flex; align-items: center; gap: 8px;
    font-size: 24px; font-weight: 500; letter-spacing: .4px;
  }
  .person__role { margin-left: 26px; margin-top: 2px; font-size: 20px; }
  .rule { position: absolute; left: 18px; top: 129px; width: 261px; height: 3px; background: var(--red); }

  .contacts { position: absolute; left: 20px; top: 155px; list-style: none; }
  .contacts li {
    display: flex; align-items: center; gap: 6px;
    height: 23.8px; font-size: 14px; word-spacing: 2px;
  }
  .icon { width: 16px; height: 16px; flex: none; }

  .services { position: absolute; left: 30px; top: 81px; list-style: none; }
  .services li {
    display: flex; align-items: center; gap: 8px;
    font-size: 15.5px; word-spacing: 3px; line-height: 1;
  }
  .services li:nth-child(2) { margin-top: 8px; }
  .services li:nth-child(3) { margin-top: 10px; }
  .services li:nth-child(4) { margin-top: 7px; }
  .services li:nth-child(5),
  .services li:nth-child(6) { margin-top: 9px; }
  .dot { width: 7px; height: 7px; border-radius: 50%; background: var(--red); flex: none; }

  .appointment { position: absolute; left: 30px; list-style: none; top: 254px; }
  .appointment li { display: flex; align-items: center; gap: 6px; font-size: 16px; height: 30px; line-height: 1; }
  .appointment .blank { width: 228px; height: 3px; background: var(--red); align-self: center; margin-top: 6px; }
</style>
</head>
<body>

<section class="card card--front" aria-label="Business card front">
  <div class="block block--top"></div>
  <div class="block block--bottom"></div>
  <div class="brand">Keelstone Prime<br>Automotive</div>

  <div class="person">
    <div class="person__name">
      <svg class="icon" style="width:22px;height:22px" viewBox="0 0 22 22" aria-hidden="true">
        <circle cx="11" cy="11" r="11" fill="var(--red)"/>
        <circle cx="11" cy="6.5" r="2.6" fill="var(--ink)"/>
        <rect x="8" y="10" width="6" height="8" rx="1.5" fill="var(--ink)"/>
      </svg>
      Marlo Fenwicke
    </div>
    <div class="person__role">(Director)</div>
  </div>
  <div class="rule"></div>

  <ul class="contacts">
    <li>
      <svg class="icon" viewBox="0 0 16 16" aria-hidden="true"><circle cx="8" cy="8" r="8" fill="var(--red)"/><path d="M5 4l2 .3.6 2-1 .8a6 6 0 0 0 2.3 2.3l.8-1 2 .6.3 2-1.2.9C7.5 11.6 4.4 8.5 4.1 5.2z" fill="var(--ink)"/></svg>
      027 451 9362
    </li>
    <li>
      <svg class="icon" viewBox="0 0 16 16" aria-hidden="true"><circle cx="8" cy="8" r="8" fill="var(--red)"/><path d="M3.5 6.5c2.5-2 6.5-2 9 0l-.8 1.3-1.7-.5V6.4H6v.9l-1.7.5z" fill="var(--ink)"/><rect x="5" y="8" width="6" height="3.5" rx=".8" fill="var(--ink)"/></svg>
      07 594 2713
    </li>
    <li>
      <svg class="icon" viewBox="0 0 16 16" aria-hidden="true"><circle cx="8" cy="8" r="8" fill="var(--red)"/><rect x="4" y="5" width="8" height="6" rx=".6" fill="var(--ink)"/><path d="M4.3 5.4 8 8.3l3.7-2.9" stroke="var(--red)" stroke-width=".9" fill="none"/></svg>
      office@keelstoneautomotive.example.nz
    </li>
    <li>
      <svg class="icon" viewBox="0 0 16 16" aria-hidden="true"><circle cx="8" cy="8" r="8" fill="var(--red)"/><circle cx="8" cy="8" r="4.8" fill="none" stroke="var(--ink)" stroke-width="1.1"/><ellipse cx="8" cy="8" rx="2" ry="4.8" fill="none" stroke="var(--ink)" stroke-width="1"/><path d="M3.2 8h9.6" stroke="var(--ink)" stroke-width="1"/></svg>
      keelstoneautomotive.example.nz
    </li>
    <li>
      <svg class="icon" viewBox="0 0 16 16" aria-hidden="true"><circle cx="8" cy="8" r="8" fill="var(--red)"/><path d="M3.5 8.2 8 4l4.5 4.2h-1.4V12H9V9.5H7V12H4.9V8.2z" fill="var(--ink)"/></svg>
      48 Tarn Lane Ravensmere 3598
    </li>
  </ul>
</section>

<section class="card card--back" aria-label="Business card back">
  <div class="block block--top"></div>
  <div class="block block--bottom"></div>
  <div class="brand">Keelstone Prime<br>Automotive</div>

  <ul class="services">
    <li><span class="dot"></span>Vehicle Servicing</li>
    <li><span class="dot"></span>All Mechanical Repairs</li>
    <li><span class="dot"></span>Warrant of Fitness</li>
    <li><span class="dot"></span>Tyres &amp; Wheel Alignments</li>
    <li><span class="dot"></span>Automotive Parts &amp; Supplies</li>
    <li><span class="dot"></span>Automotive Diagnostics</li>
  </ul>

  <ul class="appointment">
    <li><span class="dot"></span>Date<span class="blank"></span></li>
    <li><span class="dot"></span>Time<span class="blank"></span></li>
  </ul>
</section>

</body>
</html>
```